Marlow Estate Fixers (Handyman / Home Improvement Company)

Looking for a double sided professional looking business card with Logo attached to be highlighted on one side and throwing in an image of a handyman as an option would be nice to see as well. We are a company focused on providing quality Handyman and Home improvement services in a timely manner that is done right the first time with integrity

Industry/Entity Type

Handyman / Home Improvement

Contact Information for Business Card

(LOGO, Name, Mobile and office phone numbers, email) on front side of card, (the words "The SOLUTION to all of your Handyman and Home Improvement needs" followed by "Family Owned and Operated" at the very bottom) on the back.

Colors
EB3D1F
EC4F4E
F09395
F8D3D4
FCEDEE

Requirements
Must have
• Red, Gray, Black Color scheme
Should not have
• No Yellow or Blue colors

```html
<!DOCTYPE html>
<html lang="en">
<head>
<meta charset="utf-8">
<title>Marlow Estate Fixers – Business Card</title>
<link href="https://fonts.googleapis.com/css2?family=Poppins:wght@400;500;600&display=swap" rel="stylesheet">
<style>
  :root {
    --page: #f1f1f1;
    --card: #222226;
    --red: #ed1c24;
    --white: #ffffff;
    --emboss: #141416;
  }
  html, body {
    margin: 0;
    padding: 0;
    width: 1200px;
    height: 990px;
    overflow: hidden;
    background: var(--page);
    font-family: "Poppins", sans-serif;
  }
  .card {
    position: absolute;
    left: 244px;
    width: 712px;
    height: 406px;
    background: var(--card);
    border-left: 5px solid var(--red);
    border-bottom: 4px solid var(--red);
    box-sizing: border-box;
    box-shadow: 0 14px 28px rgba(0,0,0,0.28);
    color: var(--white);
  }
  .card--front { top: 68px; }
  .card--back { top: 515px; }

  /* Front side */
  .brand-mark {
    position: absolute;
    left: 0;
    right: 0;
    top: 150px;
    text-align: center;
    font-weight: 600;
    font-size: 40px;
    color: var(--emboss);
    letter-spacing: 1px;
  }
  .tagline {
    position: absolute;
    left: 0;
    right: 0;
    text-align: center;
    margin: 0;
  }
  .tagline--family { top: 334px; color: var(--red); font-size: 17px; }
  .tagline--promise { top: 356px; font-size: 16px; letter-spacing: 0.4px; }

  /* Back side */
  .brand-lockup {
    position: absolute;
    left: 27px;
    top: 70px;
    display: flex;
    align-items: center;
    gap: 10px;
  }
  .brand-lockup__square {
    width: 22px;
    height: 22px;
    background: var(--red);
  }
  .brand-lockup__name {
    font-weight: 600;
    font-size: 24px;
    color: var(--red);
    line-height: 1.1;
  }
  .person {
    position: absolute;
    right: 30px;
    top: 26px;
    text-align: right;
  }
  .person__name {
    margin: 0;
    font-size: 40px;
    line-height: 1.1;
    color: var(--red);
    font-weight: 400;
  }
  .person__name strong { font-weight: 600; }
  .person__role {
    margin: 0;
    font-size: 20px;
    font-weight: 500;
  }
  .accent-bar {
    position: absolute;
    right: 0;
    top: 31px;
    width: 20px;
    height: 63px;
    background: var(--red);
  }
  .address {
    position: absolute;
    left: 21px;
    top: 206px;
    margin: 0;
    font-style: normal;
    font-size: 20px;
    line-height: 27px;
    letter-spacing: 0.5px;
  }
  .contact-list {
    position: absolute;
    left: 21px;
    top: 284px;
    margin: 0;
    padding: 0;
    list-style: none;
    font-size: 19px;
    line-height: 24.3px;
    letter-spacing: 0.5px;
  }
  .contact-list li { display: flex; align-items: center; gap: 10px; }
  .contact-list svg { width: 17px; height: 17px; flex: none; }
  .contact-list .hl { color: var(--red); }
</style>
</head>
<body>

<section class="card card--front">
  <div class="brand-mark">Marlow Estate Fixers</div>
  <p class="tagline tagline--family">Family Owned and Operated</p>
  <p class="tagline tagline--promise">Your SOLUTION to all of your Handyman and Home Improvement needs</p>
</section>

<section class="card card--back">
  <div class="brand-lockup">
    <span class="brand-lockup__square"></span>
    <span class="brand-lockup__name">Marlow Estate Fixers</span>
  </div>

  <div class="person">
    <h1 class="person__name"><strong>Daria</strong> Kellner</h1>
    <p class="person__role">Founder &amp; CEO</p>
  </div>
  <div class="accent-bar"></div>

  <address class="address">418 Brookfield Ave. Suite 12<br>Arden, TX 75001</address>

  <ul class="contact-list">
    <li>
      <svg viewBox="0 0 24 24" fill="none" stroke="#ed1c24" stroke-width="2"><rect x="6" y="1.5" width="12" height="21" rx="2"/><line x1="10" y1="19" x2="14" y2="19"/></svg>
      <span>(555) 214-3698</span>
    </li>
    <li>
      <svg viewBox="0 0 24 24" fill="#ed1c24"><path d="M6.6 10.8a15 15 0 0 0 6.6 6.6l2.2-2.2a1 1 0 0 1 1-.25 11.4 11.4 0 0 0 3.6.57 1 1 0 0 1 1 1V20a1 1 0 0 1-1 1A17 17 0 0 1 3 4a1 1 0 0 1 1-1h3.5a1 1 0 0 1 1 1c0 1.25.2 2.45.57 3.57a1 1 0 0 1-.25 1z"/></svg>
      <span>(555) 214-0000</span>
    </li>
    <li>
      <svg viewBox="0 0 24 24" fill="none" stroke="#ed1c24" stroke-width="2"><circle cx="12" cy="12" r="10"/><path d="M2 12h20M12 2a15 15 0 0 1 0 20M12 2a15 15 0 0 0 0 20"/></svg>
      <span>www.<span class="hl">marlowfixers</span>.com</span>
    </li>
    <li>
      <svg viewBox="0 0 24 24" fill="#ed1c24"><path d="M2 9l10 6 10-6v12H2z"/><path d="M2 8l10-6 10 6-10 6z" opacity="0.7"/></svg>
      <span>info@<span class="hl">marlowfixers</span>.com</span>
    </li>
  </ul>
</section>

</body>
</html>
```